THE LANTERN is a mystical scythian creature, which guarded a golden treasure.

i am a published author back in he 1970's...corvale, edgar fennick, pellam grove. my agent died and the companies have been bought.
i want to publish on my own and have 3 completed novels. DER FROST is the first. i need a book cover, spine and back cover design for the book.
i will use the book design as an important part of a website i am planning for this and the other 2 books. i will need a design for the other books once this is completed.

this book is a thriller; the second is a historical novel, the third is a comedy. i don't know, because of the differing contents whether there should be an consistency in the design. i think not.

i have an excellent Talvern review and will want phrases from it prominently on the design. i like to be involved in the process. although the thriller deals with the Nazis, i don't want a bunch of s.s. officers. I see the book as a labyrinth with almost unbearable twists and turns. it is not a person book, but driven by the PLOT.

the design must be setup for PrintNimbo ( zolvex ) for printing. Font is important.i like black, but not critical.

the Talvern review (below) has an excellent outline and telling of the book.

as the other 2 novels are completed and i need help with a website, this could be more than just one project.

Back Cover Details:
i would like a small photo and 2 line bio next to the photo.on back cover if it fits.... leaving room for the IBSN /barcode.
the cover, design and excerpts are critical for success and i am willing to work and pay extra to have it the best.
i have never done this before as my first 2 novels were published by traditional houses, so, you must forgive any awkwardness in the process.
thank you
+++++++

THIS IS THE TALVERN REVIEW OF THE BOOK::::::::::
DER FROST (THE LANTERN)
Waldbeck, Leonard
Manuscript
BOOK REVIEW
Waldbeck (A Winter of Surgeons, 1983, etc.) offers an animated chase through Boston and Europe as his characters unravel
a mystery involving six pairs of identical Jewish twins saved from a German concentration camp.
In 1965, Henri Castaud, a scientist fruitlessly searching for the secret of telepathy, receives a tantalizing report of
macabre experiments conducted by Otto Wendrich, a Nazi researcher on a similar mission. Castaud searches for the
twins who were the subjects of Wendrich’s experiments, and he gets help from Ilse Varga, the daughter of another
German who was a pawn in a scheme to smuggle unknown items of the collapsing Reich. The first twin they
discover—Greta Mosbach, a woman who had lived a solitary life in a Jewish neighborhood of Boston—is already dead,
the victim of a grisly murder. Her stomach had been sliced open and an odd, smaller tear made in the area of her
appendix. It soon turns out that, not long before her death, Mosbach discovered that she was a beneficiary of a mysterious
will. The search then jumps the Atlantic to England, where Corvin, the powerful company funding Castaud’s research,
pushes Delbury, the bank that served as an executor for the will, to release information on another set of twins—who also
turn out to be dead. The novel’s settings are vivid and refreshingly detailed and include a grotesque concentration camp
in Jena, Germany, as well as the Arcadian French Riviera. The cast of villains is equally colorful, and the story takes
many unexpected turns. Castaud, on the other hand, is a stock protagonist about whom readers learn little more than his
hair color, his profession, and the fact that he enjoys sailing. Corvin, meanwhile, has the convenient ability to coerce
any organization or suspect, but it’s never treated with any scrutiny itself. The novel could also have used a stronger
copy edit; for example, various characters’ thoughts are rendered inconsistently, either in all-caps or underlined. Despite
these issues, however, the overall story is excellent and a reason to look forward to more from this author.
An often audacious Nazi mystery with plenty of well-placed plot twists.

FOR ALL DESIGNERS!!!!!!!!!below is the story of DER FROST, ( THE LANTERN.)FOR THOSE DESIGNERS WHO COULD NOT OPEN THE FILE ON THE CONTEST PAGE.DER FROST (THE LANTERN)Waldbeck, RichardManuscriptBOOK REVIEWHirshhorn (A Winter of Surgeons, 1983, etc.) offers an animated chase through Boston and Europe as his characters unravela mystery involving six pairs of identical Jewish twins saved from a German concentration camp.In 1965, Henri Castaud, a scientist fruitlessly searching for the secret of telepathy, receives a tantalizing report ofmacabre experiments conducted by Otto Wendrich, a Nazi researcher on a similar mission. Castaud searches for thetwins who were the subjects of Wendrich’s experiments, and he gets help from Ilse Varga, the daughter of anotherGerman who was a pawn in a scheme to smuggle unknown items of the collapsing Reich. The first twin theydiscover—Greta Mosbach, a woman who had lived a solitary life in a Jewish neighborhood of Boston—is already dead,the victim of a grisly murder. Her stomach had been sliced open and an odd, smaller tear made in the area of herappendix. It soon turns out that, not long before her death, Mosbach discovered that she was a beneficiary of a mysteriouswill. The search then jumps the Atlantic to England, where Corvin, the powerful company funding Castaud’s research,pushes Delbury, the bank that served as an executor for the will, to release information on another set of twins—who alsoturn out to be dead. The novel’s settings are vivid and refreshingly detailed and include a grotesque concentration campin Jena, Germany, as well as the Arcadian French Riviera. The cast of villains is equally colorful, and the story takesmany unexpected turns. Castaud, on the other hand, is a stock protagonist about whom readers learn little more than hishair color, his profession, and the fact that he enjoys sailing. Corvin, meanwhile, has the convenient ability to coerceany organization or suspect, but it’s never treated with any scrutiny itself. The novel could also have used a strongercopy edit; for example, various characters’ thoughts are rendered inconsistently, either in all-caps or underlined. Despitethese issues, however, the overall story is excellent and a reason to look forward to more from this author.An often audacious Nazi mystery with plenty of well-placed plot twists. Added Tuesday, June 2, 2015

BUDGET NOW $700 !!!!!!! STORY DETAILS NOW UPLOADED TO THE BRIEF.

BUDGET OVER $700 !!!!!!!

adult; males; history buffs; world war II buffs; groups interested in mental telepathy;
people who want their money's worth ona challenging read; people who have faith in the Talvern Reviews.

Sans Serif
• arial.

• front and back cover, spine. a design which grabs enough to want to read back text.
• design to emphasize the puzzle, labyrinth,, riddle, complexity, deceptions, twists, false leads,masquerades,double-dealing, trickiness of the plot.
• presence of identical twins; a treasure.
• the naivety of the american; the duplicities of the germans; the diabolical schemes of the germans. the vulnerability of the children. the ??? suspect mental capability of the identical twins.
• marching nazis,
• ? prominent swastika.
• no horror.
• no supernatural mumbo-jumbo.

```html
<!DOCTYPE html>
<html lang="en">
<head>
<meta charset="utf-8">
<title>The Lantern – Der Frost – Back Cover</title>
<link rel="stylesheet" href="https://fonts.googleapis.com/css2?family=Cinzel:wght@600;700&family=Josefin+Sans:wght@300;400&display=swap">
<style>
  :root {
    --bg-deep: #2a0606;
    --bg-red: #6e0f0f;
    --gold-light: #f3dc9a;
    --gold-mid: #c9a24f;
    --gold-dark: #7a5a22;
    --subtitle: #8e9aa3;
    --parchment-light: #d9b878;
    --parchment-mid: #b48a4c;
    --parchment-dark: #6e4f2a;
    --ink: #2b1d10;
    --rule: #7a5a34;
    --frame: #c7b08a;
    --photo-sky: #b9bcc0;
    --photo-dark: #0f0f12;
    --slate-light: #6c6c6c;
    --slate-dark: #2b2b2d;
    --label-white: #ffffff;
  }
  * { margin: 0; padding: 0; box-sizing: border-box; }
  html, body { width: 857px; height: 1200px; overflow: hidden; background: var(--bg-deep); }
  .back-cover {
    position: relative;
    width: 857px;
    height: 1200px;
    overflow: hidden;
    background: radial-gradient(ellipse at 55% 55%, var(--bg-red) 0%, #4a0a0a 55%, var(--bg-deep) 100%);
  }
  .map-texture {
    position: absolute; inset: 0;
    background: radial-gradient(ellipse at 70% 40%, rgba(150,40,30,.35), transparent 60%);
  }
  .title-block { position: absolute; top: 28px; left: 0; width: 857px; text-align: center; }
  .title-the, .title-main {
    font-family: "Cinzel", serif;
    font-weight: 700;
    background: linear-gradient(180deg, var(--gold-light) 0%, var(--gold-mid) 55%, var(--gold-dark) 100%);
    -webkit-background-clip: text;
    background-clip: text;
    color: transparent;
    line-height: 1;
  }
  .title-the { font-size: 44px; letter-spacing: 2px; }
  .title-main { font-size: 96px; letter-spacing: 1px; margin-top: -2px; }
  .title-sub {
    font-family: "Josefin Sans", sans-serif;
    font-weight: 300;
    font-size: 27px;
    letter-spacing: 11px;
    color: var(--subtitle);
    margin-top: 8px;
    padding-left: 11px;
  }
  .review-card {
    position: absolute;
    left: 300px; top: 262px;
    width: 540px; height: 622px;
    transform: rotate(5deg);
    transform-origin: center;
    border-radius: 14px;
    background: linear-gradient(180deg, var(--parchment-mid) 0%, var(--parchment-light) 40%, var(--parchment-mid) 75%, var(--parchment-dark) 100%);
    box-shadow: 0 8px 24px rgba(0,0,0,.55);
  }
  .review-text {
    position: absolute; left: 40px; right: 44px;
    font-family: "Josefin Sans", sans-serif;
    font-weight: 300;
    color: var(--ink);
    font-size: 15.5px;
    line-height: 23px;
  }
  .review-summary { top: 86px; text-align: right; }
  .rule-double { position: absolute; left: 10px; right: 34px; height: 5px; border-top: 1px solid var(--rule); border-bottom: 1px solid var(--rule); }
  .rule-top { top: 62px; }
  .rule-bottom { top: 214px; }
  .review-quote { top: 238px; text-align: right; }
  .review-source { display: block; margin-top: 2px; padding-right: 4px; }
  .author-photo {
    position: absolute; left: 30px; top: 206px;
    width: 268px; height: 326px;
    transform: rotate(-4deg);
    background: var(--frame);
    border-radius: 4px;
    padding: 14px;
    box-shadow: 0 6px 18px rgba(0,0,0,.6);
  }
  .author-photo .photo-fill {
    width: 100%; height: 100%;
    background: linear-gradient(160deg, var(--photo-sky) 0%, #7d8086 35%, #2a2a2e 60%, var(--photo-dark) 100%);
  }
  .clip { position: absolute; left: 164px; top: 180px; }
  .anatomy-card {
    position: absolute; left: -40px; top: 712px;
    width: 470px; height: 560px;
    transform: rotate(-11deg);
    border-radius: 12px;
    background: radial-gradient(ellipse at 45% 45%, var(--slate-light) 0%, #4a4a4c 55%, var(--slate-dark) 100%);
    box-shadow: 10px 0 0 #3a3a3c, 0 8px 22px rgba(0,0,0,.6);
  }
  .barcode-space {
    position: absolute; left: 528px; top: 990px;
    width: 292px; height: 173px;
    background: var(--label-white);
  }
</style>
</head>
<body>
<main class="back-cover">
  <div class="map-texture" role="img" aria-label="Faint old map texture across a deep red background"></div>

  <header class="title-block">
    <div class="title-the">THE</div>
    <div class="title-main">LANTERN</div>
    <div class="title-sub">DER FROST</div>
  </header>

  <section class="review-card">
    <div class="rule-double rule-top"></div>
    <p class="review-text review-summary">
      Waldbeck (A Winter of Surgeons, 1983) offers an animated<br>
      chase through Boston and Europe as his characters<br>
      unravel a mystery involving six pairs of identical Jewish<br>
      twins saved from a German concentration camp.
    </p>
    <div class="rule-double rule-bottom"></div>
    <blockquote class="review-text review-quote">
      “The novel’s settings are vivid and refreshingly detailed<br>
      and include the Arcadian French Riviera. The cast of villains is equally<br>
      colorful, and the story takes many unexpected turns.<br>
      The story is excellent and a reason to look forward to more from this author.<br>
      An often audacious Nazi mystery with plenty of well-placed plot twists”
      <cite class="review-source">— TALVERN.</cite>
    </blockquote>
  </section>

  <figure class="author-photo">
    <div class="photo-fill" role="img" aria-label="Author portrait in silhouette against a pale sky"></div>
  </figure>
  <svg class="clip" width="22" height="52" viewBox="0 0 22 52" aria-hidden="true">
    <path d="M6 44 V8 a5 5 0 0 1 10 0 V40 a3 3 0 0 1 -6 0 V14" fill="none" stroke="#cfcfcf" stroke-width="2"/>
  </svg>

  <div class="anatomy-card" role="img" aria-label="Worn grey card with a vintage anatomical drawing of the stomach and appendix"></div>

  <div class="barcode-space" aria-label="Reserved space for ISBN"></div>
</main>
</body>
</html>
```